Business card design for a dynamic IT consulting company

We need a business card design for a young firm, specialized in the Telecommunications/Consulting industry. The name of the company is Quindor and Partners Business Consulting Ltd. (Short name: Quindor and Partnes)
Quindor = solve read reverse, so we aim to be uncomplicated and solution-oriented. The small pipe in our logo is also related to the word solve. So we need a new business card design, which is simple, eye catching and something non traditional (I would probably prefer a square shaped design rather than a rectangle, but open for suggestions). Attached our logo.

Target Market(s)

Usually our customers are Tier1 Telecoms providers (Q-Netra, Palorix, etc) and their executives.

Industry/Entity Type

Business

Contact Information for Business Card

Name: Bence Tolnavari
Email: b.tolnavari@quindor.hu
Web: www.quindor.hu
Mobile: +36 30 518 2769
Title: Managing Director

Optional:
Company name: Quindor and Partners Ltd.
Address: 1087 Budapest, Tolvenka str. 28/C, Hungary

Font styles to use
Other font styles liked:
• helveticaneue_medium, Prime Regular are used now.

Colors

Designer to choose colors to be used in the design.

Requirements
Must have
• I would like to have a 2 sided design.
Nice to have
• I thought if we make the logo a bit bigger (without the company name), that could go to the back with the company name below. I though, if the pipe in the logo is somehow touchable on the business card, would be nice and unique.

```html
<!DOCTYPE html>
<html lang="en">
<head>
<meta charset="utf-8">
<title>Quindor &amp; Partners – Business Card</title>
<link rel="stylesheet" href="https://fonts.googleapis.com/css2?family=Arimo:wght@400;700&display=swap">
<style>
  :root {
    --backdrop: #e4e4e4;
    --card: #f7f7f7;
    --ink: #58585a;
    --ink-soft: #6d6d6f;
    --blue: #0a98d6;
    --magenta: #b0308a;
    --band: #58585a;
    --white: #ffffff;
  }
  * { box-sizing: border-box; margin: 0; padding: 0; }
  html, body { width: 1200px; height: 960px; overflow: hidden; }
  body {
    background: var(--backdrop);
    font-family: "Arimo", Arial, sans-serif;
    color: var(--ink);
    position: relative;
  }
  .card {
    position: absolute;
    top: 305px;
    width: 343px;
    height: 343px;
    background: var(--card);
    overflow: hidden;
  }
  .card--front { left: 200px; }
  .card--back { left: 651px; }

  .brand { position: absolute; left: 0; right: 0; text-align: center; }
  .brand__row { display: flex; align-items: center; justify-content: center; gap: 8px; }
  .brand__mark { width: 12px; height: 12px; background: var(--magenta); }
  .brand__name { font-weight: 400; color: var(--ink); letter-spacing: 0.2px; line-height: 1; }
  .brand__tagline { color: var(--ink); font-weight: 700; line-height: 1; }

  .card--front .brand { top: 38px; }
  .card--front .brand__name { font-size: 25px; }
  .card--front .brand__tagline { font-size: 8px; letter-spacing: 3.4px; margin-top: 3px; padding-left: 20px; }

  .person { position: absolute; top: 104px; left: 0; right: 0; text-align: center; }
  .person__name { font-size: 18px; font-weight: 700; color: var(--blue); letter-spacing: 0.3px; }
  .person__title { font-size: 14px; color: var(--ink-soft); margin-top: 3px; letter-spacing: 0.3px; }

  .address { position: absolute; top: 169px; left: 0; right: 0; text-align: center; font-size: 13.5px; line-height: 19px; color: var(--ink); }

  .contact-band {
    position: absolute; left: 0; bottom: 0; width: 343px; height: 108px;
    background: var(--band);
  }
  .contact-list { position: absolute; left: 29px; top: 20px; list-style: none; }
  .contact-list li { display: flex; align-items: center; gap: 8px; color: var(--white); font-size: 13.5px; line-height: 18px; }
  .contact-list svg { width: 11px; height: 11px; flex: none; }

  .pattern-area {
    position: absolute; right: 0; bottom: 0; width: 145px; height: 108px;
    background: linear-gradient(135deg, #f7f7f7 0%, #dfeef7 45%, #f1dcea 100%);
    border-top-left-radius: 28px;
  }

  .card--back .brand { top: 30px; }
  .card--back .brand__name { font-size: 31px; }
  .card--back .brand__tagline { font-size: 9px; letter-spacing: 5px; margin-top: 3px; }
  .brand__web { font-size: 13px; letter-spacing: 10.5px; color: var(--ink); margin-top: 6px; font-weight: 700; line-height: 1; padding-left: 10px; }

  .faint-pattern {
    position: absolute; left: 30px; top: 112px; width: 283px; height: 212px;
    background: linear-gradient(135deg, #f4e8f0 0%, #e6f1f8 50%, #eeeeee 100%);
  }
</style>
</head>
<body>

  <section class="card card--front" aria-label="Business card, front">
    <header class="brand">
      <div class="brand__row">
        <span class="brand__mark"></span>
        <span class="brand__name">Quindor &amp; Partners</span>
      </div>
      <p class="brand__tagline">SIMPLE · SMART · SOLVED</p>
    </header>

    <div class="person">
      <h1 class="person__name">BENCE TOLNAVARI</h1>
      <p class="person__title">MANAGING DIRECTOR</p>
    </div>

    <p class="address">Quindor and Partners Ltd., 1087 Budapest<br>Tolvenka str. 28/C, Hungary</p>

    <div class="contact-band">
      <ul class="contact-list">
        <li>
          <svg viewBox="0 0 11 11" aria-hidden="true"><rect x="2.5" y="0.5" width="6" height="10" rx="1" fill="none" stroke="#fff" stroke-width="1.2"/><rect x="4.5" y="8.3" width="2" height="1" fill="#fff"/></svg>
          +36 30 518 2769
        </li>
        <li>
          <svg viewBox="0 0 11 11" aria-hidden="true"><rect x="0.5" y="2" width="10" height="7" fill="#fff"/><path d="M0.5 2 L5.5 6 L10.5 2" fill="none" stroke="#58585a" stroke-width="1"/></svg>
          b.tolnavari@quindor.hu
        </li>
        <li>
          <svg viewBox="0 0 11 11" aria-hidden="true"><circle cx="5.5" cy="5.5" r="5" fill="#fff"/><path d="M3 3.5 Q5 3 5 5 Q3.5 6 4 8.5 M7 2 Q6.5 4 8.5 5 Q9 7 7.5 8.5" fill="none" stroke="#58585a" stroke-width="0.9"/></svg>
          www.quindor.hu
        </li>
      </ul>
      <div class="pattern-area" role="img" aria-label="Decorative pattern of small coloured squares in magenta, blue and grey"></div>
    </div>
  </section>

  <section class="card card--back" aria-label="Business card, back">
    <header class="brand">
      <div class="brand__row">
        <span class="brand__name">Quindor &amp; Partners</span>
      </div>
      <p class="brand__tagline">SIMPLE · SMART · SOLVED</p>
      <p class="brand__web">www.quindor.hu</p>
    </header>
    <div class="faint-pattern" role="img" aria-label="Large faint pattern of pale pink, blue and grey squares"></div>
  </section>

</body>
</html>
```